Staff Newsletter Template Image

We are looking for two .jpg images that we can put into a Word document and use for our staff newsletter. We will then add content using text boxes.
Attached is the current template which works for the columns and size that we need but we just want a fresh new design.
The Word document shows how we use it.
The name will stay the same - Brightwave Post but can be a different look to the current one.

Target Market(s)

Sales team

Colors

Designer to choose colors to be used in the design.

Requirements
Must have
• Colours will be green, grey and white, possibly cream if needed. All from the guidelines.
• I have attached our brand guidelines which shows design elements and fonts for our brand. Also attached is brand guidelines for one of our product lines as we would like to use the same green.
• It needs to be nice to look at and motivational for our team

```html
<!DOCTYPE html>
<html lang="en">
<head>
<meta charset="utf-8">
<title>Brightwave Post – Staff Newsletter</title>
<link href="https://fonts.googleapis.com/css2?family=Jost:wght@400;500&display=swap" rel="stylesheet">
<style>
  :root {
    --backdrop: #2b2d2b;
    --leaf: #4f7d4a;
    --sage: #86a973;
    --mist: #d5e1c8;
    --paper: #ffffff;
    --slate: #4a4d4b;
    --ink: #1f2420;
    --muted: #a6aaa7;
    --footer-text: #d2d5d2;
  }
  * { box-sizing: border-box; margin: 0; padding: 0; }
  html, body { width: 1200px; height: 960px; overflow: hidden; }
  body {
    background: var(--backdrop);
    font-family: "Jost", "Futura", sans-serif;
    position: relative;
  }
  .page {
    position: absolute;
    top: 147px;
    width: 472px;
    height: 666px;
    overflow: hidden;
    background: var(--paper);
  }
  .page--front { left: 80px; }
  .page--back { left: 636px; background: var(--leaf); }

  /* Front header */
  .masthead { position: absolute; left: 0; top: 0; width: 472px; height: 109px; }
  .masthead svg { position: absolute; inset: 0; }
  .masthead__name {
    position: absolute; left: 33px; top: 48px;
    font-size: 22px; font-weight: 500; color: var(--ink); letter-spacing: 0.5px;
  }
  .masthead__date {
    position: absolute; left: 315px; top: 28px;
    font-size: 17px; font-weight: 400; color: var(--paper);
  }
  .feature-band { position: absolute; left: 0; top: 109px; width: 472px; height: 165px; background: var(--leaf); }
  .feature {
    position: absolute; left: 27px; top: 140px; width: 417px; height: 252px;
    background: var(--paper); padding: 17px 19px;
    box-shadow: 0 3px 6px rgba(0,0,0,0.12);
  }
  .feature p {
    font-size: 10.2px; line-height: 17.1px; color: var(--muted);
  }
  .feature p + p { margin-top: 5px; }

  .panel {
    position: absolute; top: 417px; width: 204px; height: 154px;
    background: var(--mist); color: var(--ink); text-align: center;
    padding: 6px 7px;
  }
  .panel--sellers { left: 25px; }
  .panel--tip { left: 240px; padding: 6px 12px; }
  .panel__title { font-size: 11px; font-weight: 500; line-height: 15px; }
  .panel__text { font-size: 9px; line-height: 16px; margin-top: 2px; }
  .panel--tip .panel__text { margin-top: 4px; }
  .panel__text u { font-weight: 500; }

  .sellers { width: 190px; margin-top: 11px; border-collapse: collapse; font-size: 10px; color: var(--paper); }
  .sellers th, .sellers td { background: var(--leaf); height: 16px; border: 1.5px solid var(--mist); font-weight: 400; }
  .sellers .rank { width: 27px; }

  .footer {
    position: absolute; left: 0; bottom: 0; width: 472px; height: 76px;
    background: var(--slate); color: var(--footer-text);
  }
  .copyright { position: absolute; top: 32px; font-size: 9.5px; }
  .page--front .copyright { left: 250px; }
  .page--back .copyright { left: 0; width: 472px; text-align: center; }
  .shout-out { position: absolute; left: 76px; top: 11px; width: 100px; text-align: center; }
  .shout-out__title { font-size: 11px; text-decoration: underline; }
  .shout-out__name { font-size: 9px; margin-top: 2px; }
  .shout-out__note { font-size: 8px; margin-top: 1px; }

  /* Back page */
  .card { position: absolute; top: 20px; width: 197px; height: 371px; background: var(--paper); }
  .card--news { left: 24px; }
  .card--tips { left: 250px; }
  .card__head {
    height: 37px; background: var(--sage); color: var(--paper);
    font-size: 17px; font-weight: 400; text-align: center; line-height: 38px;
  }
  .card__body { padding: 16px 18px; }
  .card__body p { font-size: 10.8px; line-height: 17.1px; color: var(--muted); }

  .note { position: absolute; top: 426px; text-align: center; color: var(--paper); }
  .note--reminders { left: 36px; width: 182px; }
  .note--team { left: 246px; width: 196px; }
  .note__title { font-size: 11px; font-weight: 500; line-height: 15px; }
  .note__text { font-size: 9.6px; line-height: 15.9px; margin-top: 2px; }
  .note--team .note__text { margin-top: 5px; padding: 0 8px; }
</style>
</head>
<body>

<section class="page page--front">
  <header class="masthead">
    <svg width="472" height="109" viewBox="0 0 472 109" aria-hidden="true">
      <rect x="0" y="0" width="472" height="109" fill="var(--paper)"/>
      <path d="M0 9 H472 V70 L268 66 C246 65 236 58 224 44 C210 28 200 18 182 18 H0 Z" fill="var(--sage)"/>
      <rect x="0" y="0" width="472" height="9" fill="var(--leaf)"/>
    </svg>
    <div class="masthead__name">Brightwave Post</div>
    <div class="masthead__date">2019/12/15</div>
  </header>

  <div class="feature-band"></div>
  <article class="feature">
    <p>Lorem ipsum dolor sit amet, consectetur adipiscing elit, sed do eiusmod tempor incididunt ut labore et dolore magna aliqua. Ut enim ad minim veniam, quis nostrud exercitation ullamco laboris nisi ut aliquip ex ea commodo consequat. Duis aute irure dolor in reprehenderit in voluptate velit esse cillum dolore eu fugiat nulla pariatur. Excepteur sint occaecat cupidatat non proident, sunt in culpa qui officia deserunt mollit anim id est laborum.</p>
    <p>Lorem ipsum dolor sit amet, consectetur adipiscing elit, sed do eiusmod tempor incididunt ut labore et dolore magna aliqua. Ut enim ad minim veniam, quis nostrud exercitation ullamco laboris nisi ut aliquip ex ea commodo consequat. Duis aute irure dolor in reprehenderit in voluptate velit esse cillum dolore eu fugiat nulla pariatur. Excepteur sint occaecat cupidatat non proident, sunt in culpa qui officia deserunt mollit anim id est laborum.</p>
  </article>

  <aside class="panel panel--sellers">
    <h2 class="panel__title">TOP SELLERS!</h2>
    <p class="panel__text">The following Brightwave team members<br>were our top sellers last week<br><u>based on completed sales</u></p>
    <table class="sellers">
      <tr><th class="rank">#</th><th>Team Member</th></tr>
      <tr><td class="rank">1</td><td>-100 Brightwave Dollars</td></tr>
      <tr><td class="rank">2</td><td>-50 Brightwave Dollars</td></tr>
      <tr><td class="rank">3</td><td>-25 Brightwave Dollars</td></tr>
    </table>
  </aside>

  <aside class="panel panel--tip">
    <h2 class="panel__title">Top Tip From our Week’s Top Seller</h2>
    <p class="panel__text">Lorem ipsum dolor sit amet, consectetur adipiscing elit, sed do eiusmod tempor incididunt ut labore et dolore magna aliqua. Ut enim ad minim veniam, quis nostrud exercitation ullamco laboris nisi ut aliquip ex ea commodo consequat.</p>
  </aside>

  <footer class="footer">
    <div class="shout-out">
      <div class="shout-out__title">Shout Out</div>
      <div class="shout-out__name">★ Name ★</div>
      <div class="shout-out__note">[Comments]</div>
    </div>
    <div class="copyright">Copyright 2019. Brightwave. All Rights Reserved.</div>
  </footer>
</section>

<section class="page page--back">
  <article class="card card--news">
    <h2 class="card__head">Company News</h2>
    <div class="card__body">
      <p>Lorem ipsum dolor sit amet, consectetur adipiscing elit, sed do eiusmod tempor incididunt ut labore et dolore magna aliqua. Ut enim ad minim veniam, quis nostrud exercitation ullamco laboris nisi ut aliquip ex ea commodo consequat. Duis aute irure dolor in reprehenderit in voluptate velit esse cillum dolore eu fugiat nulla pariatur. Excepteur sint occaecat cupidatat non proident, sunt in culpa qui officia deserunt mollit anim id est laborum.</p>
    </div>
  </article>
  <article class="card card--tips">
    <h2 class="card__head">Tips &amp; Hints</h2>
    <div class="card__body">
      <p>Lorem ipsum dolor sit amet, consectetur adipiscing elit, sed do eiusmod tempor incididunt ut labore et dolore magna aliqua. Ut enim ad minim veniam, quis nostrud exercitation ullamco laboris nisi ut aliquip ex ea commodo consequat. Duis aute irure dolor in reprehenderit in voluptate velit esse cillum dolore eu fugiat nulla pariatur. Excepteur sint occaecat cupidatat non proident, sunt in culpa qui officia deserunt mollit anim id est laborum.</p>
    </div>
  </article>

  <section class="note note--reminders">
    <h3 class="note__title">Reminders</h3>
    <p class="note__text">Lorem ipsum dolor sit amet, consectetur adipiscing elit, sed do eiusmod tempor incididunt ut labore et dolore magna aliqua. Ut enim ad minim veniam, quis nostrud exercitation ullamco laboris nisi ut aliquip ex ea commodo consequat. Duis aute irure dolor in reprehenderit in voluptate velit esse cillum dolore eu fugiat nulla pariatur.</p>
  </section>
  <section class="note note--team">
    <h3 class="note__title">Being a Brightwave Team Member Means…</h3>
    <p class="note__text">Lorem ipsum dolor sit amet, consectetur adipiscing elit, sed do eiusmod tempor incididunt ut labore et dolore magna aliqua. Ut enim ad minim veniam, quis nostrud exercitation ullamco laboris nisi ut aliquip ex ea commodo consequat. Duis aute irure dolor in reprehenderit in voluptate velit esse cillum dolore eu fugiat nulla pariatur.</p>
  </section>

  <footer class="footer">
    <div class="copyright">Copyright 2019. Brightwave. All Rights Reserved.</div>
  </footer>
</section>

</body>
</html>
```